Senior sex novelty store providing a private method for acquiring the products and knowledge

Our business supplies novelty sex products and services, specializing in the 50+ demographic. Products include sex products for individuals and couples. Services include webinars and teleseminars that address various sex and relationship issues. We are dedicated to providing discreet delivery of products and knowledge to people over 50 entering a new phase of life, facing new challenges. Our entire process from site through shipping is kept private to allow our customers the freedom to shop and learn in the privacy of their own home.

Target Market(s)

Seniors over 50 years old

Industry/Entity Type

Store

Number of Pages Required

1 page

Font styles to use
Serif

Requirements
Must have
• place for business description with a private look
Should not have
• anything sleazy

```html
<!DOCTYPE html>
<html lang="en">
<head>
<meta charset="utf-8">
<title>Velvet Years</title>
<link href="https://fonts.googleapis.com/css2?family=Lora:wght@400;600;700&display=swap" rel="stylesheet">
<style>
:root{
  --red:#c8000a;
  --ink:#222;
  --muted:#9a9a9a;
  --line:#e4e4e4;
  --band:#6b6b6b;
  --band-text:#a4a4a4;
  --white:#fff;
  --paper:#fff;
  --link:#2a4f9a;
}
*{box-sizing:border-box;margin:0;padding:0}
html,body{width:1200px;height:3015px;overflow:hidden;background:var(--paper)}
body{font-family:"Lora",serif;color:var(--ink);position:relative}

.site-header{position:absolute;left:0;top:0;width:1200px;height:74px;border-bottom:1px solid var(--line)}
.brand{position:absolute;left:50px;top:22px;font-size:23px;font-weight:700;color:var(--red);letter-spacing:.5px}
.main-nav{position:absolute;left:380px;top:29px;display:flex;gap:34px;font-size:12px;font-weight:700;letter-spacing:.4px}
.main-nav .caret{color:var(--red);font-size:9px;margin-left:3px}
.header-icons{position:absolute;left:940px;top:22px;display:flex;gap:30px}
.header-icons svg{width:26px;height:26px;stroke:var(--red);fill:none;stroke-width:1.6}

.hero{position:absolute;left:56px;top:132px;width:812px;height:470px;border-radius:4px;overflow:hidden;
  background:linear-gradient(100deg,#5e5e5e 0%,#424242 40%,#262626 70%,#333 100%)}
.hero-title{position:absolute;left:50px;top:64px;width:500px;color:var(--white);font-size:38px;line-height:54px;font-weight:400}
.hero-text{position:absolute;left:52px;top:266px;width:320px;color:var(--white);font-size:12px;line-height:17px}
.hero-btn{position:absolute;left:56px;top:340px;width:140px;height:36px;border:1px solid var(--white);border-radius:18px;color:var(--white);font-size:11px;letter-spacing:1.5px;text-align:center;line-height:34px}
.hero-dots{position:absolute;left:350px;top:436px;display:flex;gap:14px;align-items:center}
.hero-dots span{width:7px;height:7px;border-radius:50%;background:#bbb}
.hero-dots .active{width:12px;height:12px;background:none;border:2px solid var(--white)}

.sale-box{position:absolute;left:890px;top:134px;width:252px;height:312px;background:var(--red);color:var(--white);text-align:center}
.sale-box .pct{font-size:80px;font-weight:700;margin-top:38px;line-height:1}
.sale-box .label{font-size:18px;font-weight:700;margin-top:118px}

.follow{position:absolute;left:890px;top:480px;width:252px;text-align:center}
.follow h3{font-size:15px;font-weight:700}
.follow h3 span{color:var(--link)}
.follow p{font-size:11px;line-height:16px;margin:10px auto 0;width:180px}
.follow-btn{display:inline-block;margin-top:24px;width:140px;height:36px;border:1px solid #444;border-radius:18px;font-size:11px;letter-spacing:1px;line-height:34px}
.follow-btn i{display:inline-block;width:7px;height:7px;border-radius:50%;background:#444;margin-right:8px}

.products{position:absolute;left:50px;top:632px;display:grid;grid-template-columns:repeat(4,254px);grid-auto-rows:344px;column-gap:26px;row-gap:24px}
.card{border:1px solid var(--line);border-radius:4px;box-shadow:0 1px 4px rgba(0,0,0,.06);position:relative;text-align:center;background:var(--white)}
.card .photo{position:absolute;left:26px;top:24px;width:200px;height:210px;border-radius:6px}
.card .title{position:absolute;left:14px;right:14px;top:262px;font-size:12px;line-height:17px}
.card .price{position:absolute;left:0;right:0;top:312px;font-size:11px;font-weight:600;color:var(--muted)}
.card.short .title{top:270px}
.card.top-text .title{top:28px}
.card.top-text .photo{top:72px;height:200px}
.card.top-text .price{top:296px}

.p-cream{background:linear-gradient(90deg,#f4e6ec 0 46%,#5a8ad3 46% 100%)}
.p-pink{background:linear-gradient(160deg,#fdf2f7 0%,#f6c3d8 55%,#e4609a 100%)}
.p-black{background:linear-gradient(160deg,#f6f6f6 0%,#bdbdbd 50%,#3a3a3a 100%)}
.p-silver{background:linear-gradient(160deg,#fafafa 0%,#e2e2e2 55%,#bcbcbc 100%)}
.p-dark{background:linear-gradient(135deg,#f1ead9 0 42%,#2e2e2e 58% 100%)}
.p-legs{background:linear-gradient(180deg,#f5f5f5 0%,#3a3a3a 45%,#1b1b1b 100%)}
.p-jar{background:linear-gradient(180deg,#eef2fa 0 30%,#3460bd 30% 70%,#eef2fa 70% 100%)}
.p-tube{background:linear-gradient(180deg,#2a64b8 0 35%,#eaf2f8 35% 78%,#2aa79c 78% 100%)}

.category{background:var(--red);border:none;color:var(--white);text-align:center}
.category .kicker{position:absolute;left:0;right:0;top:26px;font-size:10px;letter-spacing:.5px}
.category svg{position:absolute;left:87px;top:104px;width:80px;height:80px;fill:var(--white)}
.category .name{position:absolute;left:0;right:0;top:250px;font-size:20px;font-weight:700}
.category .sub{position:absolute;left:56px;right:56px;top:284px;font-size:11px;line-height:14px}

.view-more{position:absolute;left:460px;top:2502px;width:280px;height:52px;background:var(--red);color:var(--white);font-size:12px;text-align:center;line-height:52px;border-radius:2px 2px 0 0}
.view-more svg{width:14px;height:14px;vertical-align:-2px;margin-left:24px;stroke:var(--white);fill:none;stroke-width:2}

.features{position:absolute;left:0;top:2554px;width:1200px;height:186px;background:var(--band)}
.feature{position:absolute;top:42px;width:340px}
.feature svg{position:absolute;left:0;top:8px;width:44px;height:44px;fill:var(--red)}
.feature h4{position:absolute;left:108px;top:0;color:var(--white);font-size:14px;font-weight:600;letter-spacing:.3px}
.feature p{position:absolute;left:108px;top:28px;width:220px;color:var(--band-text);font-size:11px;line-height:16px}

.site-footer{position:absolute;left:0;top:2740px;width:1200px;height:275px;font-size:11px}
.copyright{position:absolute;left:50px;top:40px}
.foot-col{position:absolute;top:40px}
.foot-col h5{font-size:11px;font-weight:700;letter-spacing:.5px;margin-bottom:22px}
.foot-col li{list-style:none;line-height:29px}
.socials{position:absolute;left:738px;top:42px;display:flex;gap:22px}
.socials span{width:12px;height:12px;border-radius:50%;background:#b0b0b0}
.socials span:last-child{background:#e8a0a6}
</style>
</head>
<body>
<header class="site-header">
  <div class="brand">VELVET YEARS</div>
  <nav class="main-nav"><span>CATEGORIES<span class="caret">▼</span></span><span>ABOUT</span><span>CONTACT</span></nav>
  <div class="header-icons">
    <svg viewBox="0 0 28 28"><circle cx="12" cy="12" r="7"/><path d="M17 17l7 7"/></svg>
    <svg viewBox="0 0 28 28"><circle cx="14" cy="10" r="6"/><path d="M4 25c1-6 5-8 10-8s9 2 10 8"/></svg>
    <svg viewBox="0 0 28 28"><path d="M14 24S4 17 4 10a5 5 0 0 1 10-2 5 5 0 0 1 10 2c0 7-10 14-10 14z"/><circle cx="22" cy="5" r="4" fill="#fff"/></svg>
    <svg viewBox="0 0 28 28"><path d="M5 10h18l-2 14H7z"/><path d="M10 10V7a4 4 0 0 1 8 0v3"/><circle cx="23" cy="5" r="4" fill="#fff"/></svg>
  </div>
</header>

<section class="hero" role="img" aria-label="Soft black and white photo of a mature couple close together">
  <h1 class="hero-title">Lorem ipsum dolor sit amet, consectetuer adipisc­ing elit.</h1>
  <p class="hero-text">Lorem ipsum dolor sit amet, consectetuer adipiscing elit.</p>
  <div class="hero-btn">VIEW MORE</div>
  <div class="hero-dots"><span class="active"></span><span></span><span></span><span></span><span></span></div>
</section>

<aside class="sale-box"><div class="pct">20%</div><div class="label">SALES</div></aside>

<aside class="follow">
  <h3>Follow us on <span>Friendbook</span></h3>
  <p>Sed ut perspiciatis unde omnis iste natus error sit</p>
  <div class="follow-btn"><i></i>FOLLOW</div>
</aside>

<main class="products">
  <article class="card"><div class="photo p-dark" role="img" aria-label="Product photo: black and cream couples massager"></div><p class="title">Lorem ipsum dolor sit amet, con­sectetuer adipiscing</p><p class="price">$ 100</p></article>
  <article class="card top-text"><p class="title">Lorem ipsum dolor sit amet, con­sectetuer adipiscing</p><div class="photo p-legs" role="img" aria-label="Product photo: black stockings"></div><p class="price">$ 100</p></article>
  <article class="card"><div class="photo p-cream" role="img" aria-label="Product photo: cream tube with blue box"></div><p class="title">Lorem ipsum dolor sit amet, con­sectetuer adipiscing</p><p class="price">$ 100</p></article>
  <article class="card"><div class="photo p-pink" role="img" aria-label="Product photo: pink beaded accessory"></div><p class="title">Lorem ipsum dolor sit amet, con­sectetuer adipiscing</p><p class="price">$ 299.99</p></article>

  <article class="card"><div class="photo p-black" role="img" aria-label="Product photo: black feather accessory"></div><p class="title">Lorem ipsum dolor sit amet, con­sectetuer adipiscing</p><p class="price">$ 659.55</p></article>
  <article class="card"><div class="photo p-silver" role="img" aria-label="Product photo: silver accessory"></div><p class="title">Lorem ipsum dolor sit amet, con­sectetuer adipiscing</p><p class="price">$ 610.09</p></article>
  <article class="card"><div class="photo p-pink" role="img" aria-label="Product photo: pink silicone ring"></div><p class="title">Lorem ipsum dolor sit amet, con­sectetuer adipiscing</p><p class="price">$ 330.55</p></article>
  <article class="card category">
    <p class="kicker">CATEGORIES</p>
    <svg viewBox="0 0 80 80"><circle cx="40" cy="58" r="9"/><circle cx="18" cy="50" r="5"/><circle cx="62" cy="50" r="5"/><circle cx="13" cy="38" r="4"/><circle cx="67" cy="38" r="4"/><circle cx="16" cy="26" r="3.5"/><circle cx="64" cy="26" r="3.5"/><circle cx="24" cy="17" r="3"/><circle cx="56" cy="17" r="3"/><circle cx="34" cy="12" r="3"/><circle cx="46" cy="12" r="3"/><circle cx="28" cy="58" r="4"/><circle cx="52" cy="58" r="4"/></svg>
    <p class="name">ACCESSORIES</p><p class="sub">At vero eos et accusamus et iusto odio</p>
  </article>

  <article class="card"><div class="photo p-pink" role="img" aria-label="Product photo: pink silicone ring"></div><p class="title">Nora Lund Oak Table With White Marble Top</p><p class="price">$ 2195.00</p></article>
  <article class="card"><div class="photo p-silver" role="img" aria-label="Product photo: silver accessory"></div><p class="title">Lorem ipsum dolor sit amet, con­sectetuer adipiscing</p><p class="price">$ 299.09</p></article>
  <article class="card"><div class="photo p-black" role="img" aria-label="Product photo: black feather accessory"></div><p class="title">Lorem ipsum dolor sit amet, con­sectetuer adipiscing</p><p class="price">$ 870.95</p></article>
  <article class="card"><div class="photo p-pink" role="img" aria-label="Product photo: pink silicone ring"></div><p class="title">Lorem ipsum dolor sit amet, con­sectetuer adipiscing</p><p class="price">$ 129.55</p></article>

  <article class="card category">
    <p class="kicker">CATEGORIES</p>
    <svg viewBox="0 0 80 80"><path d="M14 40h44v18a6 6 0 0 1-6 6H20a6 6 0 0 1-6-6z"/><ellipse cx="36" cy="38" rx="22" ry="6"/><path d="M26 32c2-8 18-8 20 0z"/><path d="M58 46l18-14 3 4-18 14z"/></svg>
    <p class="name">CREMA</p><p class="sub">At vero eos et accusamus et iusto odio</p>
  </article>
  <article class="card"><div class="photo p-cream" role="img" aria-label="Product photo: cream tube with blue box"></div><p class="title">Lorem ipsum dolor sit amet, con­sectetuer adipiscing</p><p class="price">$ 610.09</p></article>
  <article class="card short"><div class="photo p-tube" role="img" aria-label="Product photo: lubricant tube"></div><p class="title">Lorem ipsum dolor sit amet</p><p class="price">$ 330.55</p></article>
  <article class="card short"><div class="photo p-cream" role="img" aria-label="Product photo: cream tube with blue box"></div><p class="title">Lorem ipsum dolor sit amet</p><p class="price">$ 330.55</p></article>

  <article class="card short"><div class="photo p-cream" role="img" aria-label="Product photo: cream tube with blue box"></div><p class="title">Lorem ipsum dolor sit amet</p><p class="price">$ 95.00</p></article>
  <article class="card short"><div class="photo p-jar" role="img" aria-label="Product photo: jar of warming gel"></div><p class="title">Lorem ipsum dolor sit amet</p><p class="price">$ 299.99</p></article>
  <article class="card short"><div class="photo p-cream" role="img" aria-label="Product photo: cream tube with blue box"></div><p class="title">Lorem ipsum dolor sit amet</p><p class="price">$ 70.95</p></article>
  <article class="card short"><div class="photo p-jar" role="img" aria-label="Product photo: jar of warming gel"></div><p class="title">Lorem ipsum dolor sit amet</p><p class="price">$ 129.55</p></article>
</main>

<div class="view-more">VIEW MORE<svg viewBox="0 0 14 14"><path d="M3 4a5 5 0 1 1-1 4"/><path d="M1 2v3h3"/></svg></div>

<section class="features">
  <div class="feature" style="left:50px">
    <svg viewBox="0 0 44 44"><rect x="10" y="8" width="20" height="24" rx="2"/><path d="M4 4h6v30h26v4H6z"/><circle cx="12" cy="40" r="3"/><circle cx="32" cy="40" r="3"/></svg>
    <h4>LOREM IPSUM</h4><p>Plain, unmarked boxes shipped discreetly to your door, for shoppers 50+.</p>
  </div>
  <div class="feature" style="left:426px">
    <svg viewBox="0 0 44 44"><path d="M22 4l8 12h-6l-2-3-6 9-6-4z"/><path d="M36 22l4 10-14 2v4l-6-7 6-6v4l8-1z"/><path d="M8 24l6 4-4 6h10v6H6l-4-6z"/></svg>
    <h4>LOREM IPSUM</h4><p>Private webinars and teleseminars on intimacy and relationships later in life.</p>
  </div>
  <div class="feature" style="left:800px">
    <svg viewBox="0 0 44 44"><path d="M8 4h24v18a10 10 0 0 0-6 18H8z"/><rect x="16" y="2" width="8" height="5" rx="2"/><circle cx="34" cy="34" r="9"/><path d="M30 34l3 3 6-6" stroke="#6b6b6b" stroke-width="2.5" fill="none"/><path d="M12 14h16M12 20h16M12 26h10" stroke="#6b6b6b" stroke-width="2"/></svg>
    <h4>LOREM IPSUM</h4><p>Your details stay confidential, from first click to final delivery.</p>
  </div>
</section>

<footer class="site-footer">
  <p class="copyright">© Copyright</p>
  <div class="foot-col" style="left:302px"><h5>CATEGORIES</h5><ul><li>lorem ipsum</li><li>lorem ipsum</li><li>lorem ipsum</li><li>lorem ipsum</li><li>lorem ipsum</li></ul></div>
  <div class="foot-col" style="left:488px"><h5>ABOUT</h5><ul><li>Home</li><li>About Us</li><li>Shipping</li><li>Contacts</li></ul></div>
  <div class="socials"><span></span><span></span><span></span><span></span></div>
</footer>
</body>
</html>
```